TalbeckLabs needs a new rocket based website

We need a new website that will be based on our rocket ship logo. We develop innovative solutions for enterprises. We would like to see a design that when the pages scroll, the rocket launches and goes from launch through a journey, similar to how we approach our customer. We would like areas for "Who are we", "What can we do", "What have we done", "How can we help". http://www.talbecklabs.example.au is our current website

Target Market(s)

Government, Enterprise, Cloud

Industry/Entity Type

Software Service

Coding

Coded - Design and coding required

Number of Pages Required

2 page

Requirements
Must have
• We would like to see a design that when the pages scroll, the rocket launches and goes from launch through a journey, similar to how we approach our customer.
• Must have a home page and a detail page.
• Would like to see the logo/rocket animate in some way when you scroll through he page.

```html
<!DOCTYPE html>
<html lang="en">
<head>
<meta charset="utf-8">
<title>TalbeckLabs – Enterprise Software Solutions</title>
<link href="https://fonts.googleapis.com/css2?family=Montserrat:wght@400;500;600;700&family=Open+Sans:wght@400;600&display=swap" rel="stylesheet">
<style>
:root{
  --orange:#f7941d;
  --orange-deep:#e9780a;
  --orange-soft:#fbb040;
  --cloud-warm:#f9b24a;
  --ink:#2b2b2b;
  --text:#555;
  --line:#d9d9d9;
  --grey-bg:#f3f3f3;
  --white:#fff;
}
*{box-sizing:border-box;margin:0;padding:0}
html,body{width:1200px;height:4675px;overflow:hidden}
body{font-family:"Montserrat",sans-serif;color:var(--text);background:var(--white)}
.page{position:relative;width:1200px;height:4675px}

/* Hero */
.hero{position:relative;height:1030px;background:linear-gradient(180deg,#f59a22 0%,var(--orange) 55%,var(--orange-deep) 100%);overflow:hidden}
.nav{position:absolute;top:40px;left:44px;right:44px;display:flex;justify-content:space-between;align-items:center}
.brand{display:flex;align-items:center;gap:12px;color:var(--white);font-weight:700;font-size:30px}
.brand-dot{width:16px;height:16px;border-radius:50%;background:var(--white)}
.nav-links{display:flex;gap:42px;list-style:none}
.nav-links a{color:var(--white);text-decoration:none;font-size:17px;font-weight:500}
.hero-rocket{position:absolute;left:130px;top:60px;width:330px;height:830px;border-radius:160px 160px 40px 40px;background:radial-gradient(ellipse at 50% 35%,#fff6e6 0%,#fcd48f 35%,rgba(247,148,29,0) 72%)}
.hero-copy{position:absolute;left:556px;top:308px;width:560px;color:var(--white)}
.hero-copy h1{font-size:36px;line-height:46px;font-weight:700}
.hero-copy p{margin-top:38px;font-size:22px;line-height:32px;font-weight:400;opacity:.95}
.btn-outline{display:inline-block;margin-top:48px;width:292px;height:58px;border:2px solid var(--white);border-radius:30px;text-align:center;line-height:54px;color:var(--white);font-weight:700;font-size:24px;text-decoration:none}
.cloud-band{position:absolute;left:0;bottom:0;width:1200px;height:160px;background:linear-gradient(180deg,rgba(249,178,74,0) 0%,var(--cloud-warm) 45%,var(--white) 100%)}

/* Section titles */
.section-title{display:flex;justify-content:center;align-items:center;gap:14px;font-size:34px;font-weight:600;color:var(--ink)}
.section-title .accent{color:var(--orange)}
.title-mark{width:18px;height:18px;border-radius:50%;background:var(--orange)}

/* Services */
.services{position:relative;height:1670px}
.services .section-title{position:absolute;top:185px;left:0;right:0}
.service{position:absolute;width:1200px}
.service-art{position:absolute;border-radius:20px}
.service h2{font-size:40px;font-weight:500;color:var(--orange)}
.service p{margin-top:16px;font-size:21px;line-height:30px;color:var(--text);width:440px}
.service-copy{position:absolute}

/* Projects */
.projects{position:relative;height:635px;background:var(--grey-bg)}
.projects .section-title{position:absolute;top:100px;left:0;right:0}
.card{position:absolute;top:215px;width:478px;height:340px;background:var(--white);border-radius:10px;box-shadow:0 4px 16px rgba(0,0,0,.12);overflow:hidden}
.card-head{height:80px;background:var(--orange);color:var(--white);display:flex;align-items:center;justify-content:center;gap:14px;font-size:18px;font-weight:500;letter-spacing:.5px;text-transform:uppercase}
.card-seal{width:36px;height:36px;border-radius:50%;border:2px solid var(--white)}
.card-body{padding:22px 24px 0;text-align:center}
.card-body p{font-family:"Open Sans",sans-serif;font-size:15px;line-height:22px;color:#444}
.card-body h3{margin-top:10px;font-size:19px;font-weight:600;color:var(--orange)}
.card-body hr{border:0;border-top:1px solid var(--line);margin:10px 0 14px}
.features{display:grid;grid-template-columns:1fr 1fr;row-gap:12px;column-gap:14px;list-style:none;text-align:left}
.features li{display:flex;align-items:center;gap:8px;font-family:"Open Sans",sans-serif;font-size:13px;color:#333;white-space:nowrap}
.feat-icon{width:20px;height:18px;border-radius:3px;background:#3a3a5a;flex:none}
.feat-icon.alt{background:var(--orange-soft)}
.slider-arrow{position:absolute;top:355px;width:30px;height:60px;background:var(--white);display:flex;align-items:center;justify-content:center;box-shadow:0 2px 6px rgba(0,0,0,.1)}

/* Contact */
.contact{position:relative;height:545px}
.contact .section-title{position:absolute;top:110px;left:0;right:0}
.field{position:absolute;height:50px;border:1px solid var(--line);border-radius:4px;background:var(--white);font-family:"Open Sans",sans-serif;font-size:15px;font-weight:600;color:#333;padding:12px 12px}
.btn-send{position:absolute;left:478px;top:430px;width:244px;height:50px;border-radius:25px;background:var(--orange);color:var(--white);text-align:center;line-height:50px;font-size:21px;font-weight:600}

/* Map */
.map{height:427px;background:linear-gradient(135deg,#ece9e3,#e1ded7)}

/* Footer */
.footer{position:relative;height:308px;background:var(--white)}
.footer-brand{position:absolute;left:92px;top:68px;display:flex;align-items:center;gap:10px;font-size:30px;font-weight:700;color:var(--orange)}
.footer-brand .brand-dot{background:var(--orange)}
.socials{position:absolute;left:108px;top:150px;display:flex;gap:12px}
.socials span{width:18px;height:18px;border-radius:50%;background:#b9b9b9}
.footer-col{position:absolute;top:60px}
.footer-col h4{font-size:14px;font-weight:700;color:var(--ink);letter-spacing:.5px;padding-bottom:14px;border-bottom:1px solid var(--line);width:220px}
.footer-col ul{list-style:none;margin-top:14px}
.footer-col li{font-family:"Open Sans",sans-serif;font-size:14px;color:#333;line-height:22px;display:flex;gap:8px;align-items:flex-start}
.tri{width:0;height:0;border-left:7px solid #333;border-top:5px solid transparent;border-bottom:5px solid transparent;margin-top:6px}
.contact-line{margin-bottom:16px}
.footer-col p{font-family:"Open Sans",sans-serif;font-size:14px;color:#333;line-height:21px;margin-top:14px;width:250px}
.news-input{margin-top:16px;width:250px;height:34px;border-radius:4px;background:#eee;font-size:13px;color:#333;padding:8px 10px;font-family:"Open Sans",sans-serif}
.btn-sub{margin-top:12px;width:130px;height:32px;border-radius:16px;background:var(--orange);color:var(--white);font-size:12px;font-weight:700;text-align:center;line-height:32px}
.copyright{height:60px;background:#f0f0f0;text-align:center;line-height:60px;font-size:12px;font-weight:700;color:#333;letter-spacing:.4px}
</style>
</head>
<body>
<div class="page">

  <header class="hero">
    <nav class="nav">
      <div class="brand"><span class="brand-dot"></span>TalbeckLabs</div>
      <ul class="nav-links">
        <li><a href="#">Who Are We</a></li>
        <li><a href="#">What Can We Do</a></li>
        <li><a href="#">What Have We Done</a></li>
        <li><a href="#">How Can We Help</a></li>
      </ul>
    </nav>
    <div class="hero-rocket" role="img" aria-label="Glowing rocket launching upward with flame trail"></div>
    <div class="hero-copy">
      <h1>Offering the latest in enterprise architecture, design and development of bespoke software solutions</h1>
      <p>Always researching and implementing the latest technology for customers.</p>
      <a class="btn-outline" href="#">Get Started</a>
    </div>
    <div class="cloud-band" role="img" aria-label="Bank of orange and white clouds at the base of the launch"></div>
  </header>

  <section class="services">
    <h2 class="section-title"><span class="title-mark"></span>What <span class="accent">Can We Do</span></h2>

    <div class="service" style="top:330px">
      <div class="service-art" role="img" aria-label="Laptop with hand cursor and floating documents on teal circle" style="left:130px;top:0;width:290px;height:270px;background:radial-gradient(circle at 45% 55%,#23aab8 0 45%,#e8f6f8 46% 100%)"></div>
      <div class="service-copy" style="left:520px;top:80px"><h2>e-Parliament</h2><p>All of your Parliamentary software and business process needs.</p></div>
    </div>

    <div class="service" style="top:650px">
      <div class="service-copy" style="left:155px;top:90px"><h2>Cloud</h2><p>Cloud Office Suites, Migration, Security, Customisations.</p></div>
      <div class="service-art" role="img" aria-label="Isometric workspace under a blue cloud with monitors and desk" style="left:660px;top:0;width:320px;height:300px;background:linear-gradient(160deg,#6fc3f0,#c7b8f2 60%,#efeaff)"></div>
    </div>

    <div class="service" style="top:980px">
      <div class="service-art" role="img" aria-label="Businessman riding a rocket with charts and coins" style="left:140px;top:0;width:310px;height:290px;background:linear-gradient(150deg,#fff 0%,#fde3c2 40%,#cfe3f2 100%)"></div>
      <div class="service-copy" style="left:520px;top:70px"><h2>Architecture &amp; Design</h2><p>Business process design, technology strategy and architecture.</p></div>
    </div>

    <div class="service" style="top:1290px">
      <div class="service-copy" style="left:155px;top:90px"><h2>Software Development</h2><p>Software development including business apps, web and mobile.</p></div>
      <div class="service-art" role="img" aria-label="People assembling a large dashboard screen with charts" style="left:660px;top:0;width:320px;height:300px;background:linear-gradient(150deg,#3fb7e8,#5a6ee0 55%,#f48fb1)"></div>
    </div>
  </section>

  <section class="projects">
    <h2 class="section-title"><span class="title-mark"></span>What <span class="accent">Have We Done</span></h2>
    <div class="slider-arrow" style="left:0"><svg width="12" height="18" viewBox="0 0 12 18"><path d="M10 2 3 9l7 7" fill="none" stroke="#f7941d" stroke-width="3"/></svg></div>
    <div class="slider-arrow" style="right:0"><svg width="12" height="18" viewBox="0 0 12 18"><path d="M2 2l7 7-7 7" fill="none" stroke="#f7941d" stroke-width="3"/></svg></div>

    <article class="card" style="left:100px">
      <div class="card-head"><span class="card-seal"></span>Coastal Assembly</div>
      <div class="card-body">
        <p>Lorem ipsum dolor sit amet, consectetur adipiscing elit, sed do eiusmod tempor incididunt ut labore.</p>
        <h3>Work Done</h3>
        <hr>
        <ul class="features">
          <li><span class="feat-icon"></span>Access Mobile Internet</li>
          <li><span class="feat-icon alt"></span>Alert via SMS, Email &amp; App</li>
          <li><span class="feat-icon"></span>Video &amp; Rich Media Articles</li>
          <li><span class="feat-icon"></span>Social Advocacy &amp; Sharing</li>
          <li><span class="feat-icon"></span>Teams &amp; Groups</li>
          <li><span class="feat-icon alt"></span>Business Design &amp; Tech</li>
        </ul>
      </div>
    </article>

    <article class="card" style="left:632px">
      <div class="card-head">Northern State Assembly</div>
      <div class="card-body">
        <p>Lorem ipsum dolor sit amet, consectetur adipiscing elit, sed do eiusmod tempor incididunt ut labore.</p>
        <h3>Work Done</h3>
        <hr>
        <ul class="features">
          <li><span class="feat-icon"></span>Access Mobile Internet</li>
          <li><span class="feat-icon alt"></span>Alert via SMS, Email &amp; App</li>
          <li><span class="feat-icon"></span>Video &amp; Rich Media Articles</li>
          <li><span class="feat-icon"></span>Social Advocacy &amp; Sharing</li>
          <li><span class="feat-icon"></span>Teams &amp; Groups</li>
          <li><span class="feat-icon alt"></span>Business Design &amp; Tech</li>
        </ul>
      </div>
    </article>
  </section>

  <section class="contact">
    <h2 class="section-title"><span class="title-mark"></span>How <span class="accent">Can We Help</span></h2>
    <div class="field" style="left:115px;top:195px;width:315px">Your Name</div>
    <div class="field" style="left:443px;top:195px;width:315px">Your Email</div>
    <div class="field" style="left:771px;top:195px;width:314px">Your Subject</div>
    <div class="field" style="left:115px;top:260px;width:970px;height:135px">Message</div>
    <div class="btn-send">Send</div>
  </section>

  <div class="map" role="img" aria-label="Street map showing the office location with a red pin"></div>

  <footer class="footer">
    <div class="footer-brand"><span class="brand-dot"></span>TalbeckLabs</div>
    <div class="socials"><span></span><span></span><span></span><span></span><span></span></div>

    <div class="footer-col" style="left:355px">
      <h4>QUICK LINKS</h4>
      <ul>
        <li><span class="tri"></span>Who We Are</li>
        <li><span class="tri"></span>What Can We Do</li>
        <li><span class="tri"></span>What Have We Done</li>
        <li><span class="tri"></span>How Can We Help</li>
      </ul>
    </div>

    <div class="footer-col" style="left:585px">
      <h4>CONTACT</h4>
      <ul>
        <li class="contact-line"><svg width="16" height="16" viewBox="0 0 16 16"><circle cx="8" cy="8" r="7" fill="none" stroke="#f7941d" stroke-width="2"/><circle cx="8" cy="7" r="2.5" fill="#f7941d"/></svg><span>TalbeckLabs<br>Unit 4, 118 Kestrel Rd<br>Marlow, SA 5990</span></li>
        <li class="contact-line"><svg width="16" height="16" viewBox="0 0 16 16"><path d="M4 2l3 3-2 2c1 2 2 3 4 4l2-2 3 3-2 2C7 14 2 9 2 4z" fill="none" stroke="#f7941d" stroke-width="1.6"/></svg>1300 555 012</li>
        <li><svg width="16" height="16" viewBox="0 0 16 16"><rect x="1.5" y="3.5" width="13" height="9" rx="1" fill="none" stroke="#f7941d" stroke-width="1.6"/><path d="M2 4l6 5 6-5" fill="none" stroke="#f7941d" stroke-width="1.6"/></svg>info@talbecklabs.example.au</li>
      </ul>
    </div>

    <div class="footer-col" style="left:855px">
      <h4 style="width:250px">NEWSLETTER SUBSCRIPTION</h4>
      <p>Register your email address to get more information about us</p>
      <div class="news-input">Email Address</div>
      <div class="btn-sub">SUBSCRIBE</div>
    </div>
  </footer>

  <div class="copyright">COPYRIGHT © 2018 TALBECKLABS. ALL RIGHTS RESERVED.</div>
</div>
</body>
</html>
```